Creative Fitness Studio Feature Wall

Two feature walls within functional fitness studio, they need to be on brand and have a WOW factor.
Designed to inspire and motivate people to live a fit and healthy lifestyle whilst working out and bringing life to the studio, as an uplifting and inviting environment.

Please see current walls and also visit website www.velto4.com.au for inspiration.
Updates

Target Market(s)

health and fitness, healthy lifestyle

Industry/Entity Type

Fitness

Font styles to use
Other font styles liked:
• gothic

Colors

Designer to choose colors to be used in the design.

Requirements
Must have
• inspiration from website www.velto4.com.au ........... brand consistency
Nice to have
• WOW factor......... walk into the gym and it draws your attention.
Should not have
• Overly muscly people (bodybuilders)

```html
<!DOCTYPE html>
<html lang="en">
<head>
<meta charset="utf-8">
<title>Velto4 Fitness – Feature Wall</title>
<link href="https://fonts.googleapis.com/css2?family=Crimson+Text:wght@700&display=swap" rel="stylesheet">
<style>
  :root {
    --brand-green: #8dc63f;
    --brand-black: #0b0b0b;
    --paper: #ffffff;
    --pattern-grey: #efefef;
    --figure-dark: #111111;
  }
  html, body {
    margin: 0;
    padding: 0;
    width: 1200px;
    height: 800px;
    overflow: hidden;
    background: var(--paper);
  }
  .wall {
    display: block;
    width: 1200px;
    height: 800px;
  }
  .quote {
    font-family: "Crimson Text", Georgia, serif;
    font-weight: 700;
  }
  .quote-lead { font-size: 66px; }
  .quote-line { font-size: 37px; }
  .quote-line--large { font-size: 44px; }
  .on-dark { fill: var(--paper); }
  .on-light { fill: var(--brand-black); }
  .accent { fill: var(--brand-green); }
  .panel-black { fill: var(--brand-black); }
  .panel-green { fill: var(--brand-green); }
  .backdrop { fill: var(--pattern-grey); }
  .figure { fill: var(--figure-dark); }
  .figure--green { fill: var(--brand-green); }
  .brand-name {
    font-family: "Crimson Text", Georgia, serif;
    font-weight: 700;
    fill: var(--brand-black);
  }
</style>
</head>
<body>
<svg class="wall" viewBox="0 0 1200 800" width="1200" height="800" xmlns="http://www.w3.org/2000/svg">
  <!-- backdrop -->
  <rect class="backdrop" x="0" y="0" width="1200" height="800" role="img" aria-label="Faint light grey pattern of small fitness icons"/>

  <!-- diamond panels -->
  <polygon class="panel-green" points="215,290 405,590 195,800 0,800 0,400"/>
  <polygon class="panel-black" points="0,0 340,0 485,145 215,412 0,412"/>

  <!-- barbell across the panels -->
  <rect class="figure" x="170" y="486" width="290" height="42" transform="rotate(42 315 507)" role="img" aria-label="Barbell silhouette lying diagonally across the panels"/>

  <!-- push-up figure on panel edge -->
  <rect class="figure--green" x="270" y="60" width="205" height="95" role="img" aria-label="Green silhouette of a person doing a push-up"/>

  <!-- Courage -->
  <text class="quote on-dark">
    <tspan class="quote-lead" x="42" y="174">Courage</tspan>
    <tspan class="quote-line" x="42" y="208">Is What Keeps</tspan>
    <tspan class="quote-line" x="42" y="250">You Going</tspan>
  </text>

  <!-- The difference -->
  <text class="quote on-dark">
    <tspan class="quote-lead" x="42" y="475">The</tspan>
    <tspan class="quote-line" x="42" y="522">Difference</tspan>
    <tspan class="quote-line" x="42" y="568">Between</tspan>
    <tspan class="quote-line" x="42" y="614">Dreams and</tspan>
    <tspan class="quote-line" x="42" y="660">Reality is</tspan>
    <tspan class="quote-line" x="42" y="706">Called</tspan>
    <tspan class="quote-line" x="42" y="752">Action</tspan>
  </text>

  <!-- IT never gets easier -->
  <rect class="figure" x="600" y="88" width="195" height="175" role="img" aria-label="Black silhouette of a person flipping a large tyre"/>
  <text class="quote">
    <tspan class="quote-lead accent" x="517" y="242">IT</tspan>
    <tspan class="quote-line on-light" x="514" y="286">Never Gets</tspan>
    <tspan class="quote-line on-light" x="514" y="332">Easier You</tspan>
    <tspan class="quote-line on-light" x="514" y="378">Just Get</tspan>
    <tspan class="quote-line on-light" x="514" y="425">Better</tspan>
  </text>

  <!-- Clear your mind -->
  <rect class="figure" x="910" y="74" width="110" height="116" role="img" aria-label="Black kettlebell silhouette"/>
  <text class="quote">
    <tspan class="quote-lead accent" x="838" y="249">Clear</tspan>
    <tspan class="quote-line on-light" x="838" y="294">Your Mind</tspan>
    <tspan class="quote-line on-light" x="838" y="340">Of Can’t</tspan>
  </text>

  <!-- Be the best version -->
  <rect class="figure" x="568" y="494" width="110" height="157" role="img" aria-label="Black silhouette of a seated person pressing dumbbells overhead"/>
  <text class="quote">
    <tspan class="quote-lead accent" x="480" y="637">Be</tspan>
    <tspan class="quote-line on-light" x="480" y="683">The Best</tspan>
    <tspan class="quote-line--large on-light" x="480" y="734">Version</tspan>
    <tspan class="quote-line on-light" x="480" y="775">Of You</tspan>
  </text>

  <!-- Fear -->
  <rect class="figure" x="1030" y="420" width="124" height="198" role="img" aria-label="Black silhouette of a person riding an exercise bike"/>
  <text class="quote">
    <tspan class="quote-lead accent" x="838" y="503">Fear</tspan>
    <tspan class="quote-line on-light" x="838" y="549">Is What</tspan>
    <tspan class="quote-line on-light" x="838" y="594">Stop You</tspan>
  </text>

  <!-- brand name -->
  <text class="brand-name" x="985" y="722" text-anchor="middle" font-size="78" letter-spacing="4">VELTO4</text>
  <text class="brand-name" x="985" y="768" text-anchor="middle" font-size="30" letter-spacing="10">FITNESS</text>
</svg>
</body>
</html>
```